Corporate Business Card

Very professional, Modern, Not to busy, include phone address email, website
(253) 617-4930, 18761 52nd Avenue S, Kent, WA 98047, martin@plumlinegroup.com, varkoworks.com

Target Market(s)

Manufacturing

Industry/Entity Type

Aero, machining, manufacturing, Off road racing

Contact Information for Business Card

Phone, address email, website

```html
<!DOCTYPE html>
<html lang="en">
<head>
<meta charset="utf-8">
<title>Varko Works – Business Card</title>
<link rel="stylesheet" href="https://fonts.googleapis.com/css2?family=Montserrat:wght@400;500;700&display=swap">
<style>
  :root {
    --navy: #17356e;
    --red: #d6262e;
    --white: #ffffff;
    --ink: #1b1b1b;
    --silver: #c9cbcf;
    --stage: #232323;
  }
  * { box-sizing: border-box; margin: 0; padding: 0; }
  html, body {
    width: 1200px; height: 927px; overflow: hidden;
    background: var(--stage);
    font-family: "Montserrat", Arial, sans-serif;
  }
  .sheet {
    width: 1200px; height: 927px;
    display: flex; flex-direction: column; align-items: center; justify-content: center;
    gap: 40px;
  }
  .card {
    position: relative;
    width: 700px; height: 400px;
    border-radius: 26px;
    overflow: hidden;
  }

  /* Shared brand lockup */
  .brand__name {
    font-weight: 700; letter-spacing: 2px; line-height: 1;
    text-transform: uppercase; white-space: nowrap;
  }
  .brand__rule { height: 3px; }

  /* Back side */
  .card--back { background: var(--navy); }
  .card--back .brand {
    position: absolute; left: 110px; top: 140px;
    color: var(--silver);
  }
  .card--back .brand__name { font-size: 64px; }
  .card--back .brand__rule { background: var(--silver); width: 260px; margin-top: 26px; }

  /* Front side */
  .card--front { background: var(--white); }
  .card--front .sweep { position: absolute; inset: 0; }
  .card--front .brand {
    position: absolute; right: 70px; top: 44px;
    color: var(--navy);
  }
  .card--front .brand__name { font-size: 44px; }
  .card--front .brand__rule { background: var(--navy); width: 200px; margin-top: 16px; }

  .address {
    position: absolute; left: 60px; top: 112px;
    color: var(--ink); font-size: 17px; font-weight: 500; line-height: 1.4;
  }
  .contacts {
    position: absolute; left: 60px; top: 192px;
    list-style: none; color: var(--ink); font-size: 17px; font-weight: 500;
  }
  .contacts li { display: flex; align-items: center; gap: 12px; line-height: 1.6; }
  .contacts svg { width: 16px; height: 16px; flex: none; fill: var(--red); }
</style>
</head>
<body>
<main class="sheet">
  <section class="card card--back" aria-label="Card back">
    <div class="brand">
      <div class="brand__name">Varko Works</div>
      <div class="brand__rule"></div>
    </div>
  </section>

  <section class="card card--front" aria-label="Card front">
    <svg class="sweep" viewBox="0 0 700 400" preserveAspectRatio="none" aria-hidden="true">
      <path d="M0 392 C 300 380, 560 300, 700 100 L700 400 L0 400 Z" fill="var(--navy)"/>
      <path d="M0 368 C 290 356, 550 276, 690 56 L694 60 C 565 292, 300 372, 0 380 Z" fill="var(--red)"/>
    </svg>

    <div class="brand">
      <div class="brand__name">Varko Works</div>
      <div class="brand__rule"></div>
    </div>

    <p class="address">18761 52nd Avenue<br>S, Kent, WA 98047</p>

    <ul class="contacts">
      <li>
        <svg viewBox="0 0 24 24"><path d="M6.6 10.8a15.1 15.1 0 0 0 6.6 6.6l2.2-2.2c.3-.3.7-.4 1-.2 1.1.4 2.3.6 3.6.6.6 0 1 .4 1 1V20c0 .6-.4 1-1 1A17 17 0 0 1 3 4c0-.6.4-1 1-1h3.5c.6 0 1 .4 1 1 0 1.3.2 2.5.6 3.6.1.3 0 .7-.2 1z"/></svg>
        (253) 617-4930
      </li>
      <li>
        <svg viewBox="0 0 24 24"><path d="M2 5h20v14H2z"/><path d="M3.5 6.5 12 13l8.5-6.5" fill="none" stroke="#fff" stroke-width="1.5"/></svg>
        martin@plumlinegroup.com
      </li>
      <li>
        <svg viewBox="0 0 24 24"><circle cx="12" cy="12" r="10"/><path d="M2 12h20M12 2c3 3 3 17 0 20M12 2c-3 3-3 17 0 20" fill="none" stroke="#fff" stroke-width="1.3"/></svg>
        www.varkoworks.com
      </li>
    </ul>
  </section>
</main>
</body>
</html>
```